8'x8' Exhibit Backdrop for Healthcare Events focused on the 55 and older crowds

8X8 Backdrop for Exhibiting.

I also want a design for a 6' table skirt to include our logo on two sides and the logo with Hereditary Cancer Screening underneath on the front. I want the main message of Will You Give your Loved Ones The Information To Beat Cancer in Their Lives to be completely centered on the 8X8 backdrop. Hereditary Cancer Screening The Test You Take For Them in the top left corner and the purple box on the right hand side - just like the photo that has been uploaded below. I need High resolution photos around the backdrop but not so large that they overtake the main message.

Target Market(s)

55+ crowd living in Adult only communities. They have an active lifestyle

Industry/Entity Type

Healthcare

Other font styles liked:
• "The Test You Take For Them" is Comic Sans

Colors
0255a3
fbed22
ffffff

Requirements
Must have
• I am posting a photo of the exact backdrop I would like to see. There are red arrows showing where to move certain items. There is a space underneath the slogan WILL YOU GIVE YOUR LOVED ONES... where another photo will go. Add another photo underneath the slogan that you are moving up - GIVE THEM THE GIFT OF KNOWLEDGE
• See the upload section for the new photo
• Do this one exactly like I am asking for and then you can show me some of your ideas. Thanks
• THE PHOTOS UPLOADED ARE EXAMPLES. FEEL FREE TO SEARCH OUT YOUR OWN HIGH RESOLUTION PHOTOS. THANKS

```html
<!DOCTYPE html>
<html lang="en">
<head>
<meta charset="utf-8">
<title>Hereditary Cancer Screening – Exhibit Backdrop</title>
<link rel="stylesheet" href="https://fonts.googleapis.com/css2?family=Roboto:wght@500;700&family=Roboto+Condensed:wght@400;700&family=Comic+Neue:wght@700&family=Montserrat:wght@700&display=swap">
<style>
  :root {
    --navy: #1c1f6b;
    --panel: #141868;
    --green: #4cf01a;
    --ink: #0d0d0d;
    --white: #ffffff;
    --stage: #ffffff;
  }
  html, body {
    margin: 0;
    width: 1200px;
    height: 1200px;
    overflow: hidden;
    background: var(--stage);
  }
  .backdrop {
    position: relative;
    width: 1200px;
    height: 1200px;
    background: var(--white);
    font-family: "Roboto", Arial, sans-serif;
  }
  .photo { position: absolute; }

  /* Title block */
  .title-block {
    position: absolute;
    left: 30px; top: 55px;
    width: 320px;
    text-align: right;
    color: var(--navy);
    line-height: 1;
  }
  .title-block .line { display: block; font-size: 64px; font-weight: 500; letter-spacing: -0.5px; }
  .title-block .line--bold { font-weight: 700; }
  .title-block .line + .line { margin-top: 4px; }
  .tagline {
    display: block;
    margin-top: 14px;
    background: var(--green);
    color: var(--white);
    font-family: "Comic Neue", "Comic Sans MS", cursive;
    font-weight: 700;
    font-size: 19px;
    text-align: center;
    padding: 2px 0;
  }

  /* Photo placements */
  .photo--family-top { left: 372px; top: 18px; width: 362px; height: 290px; background: linear-gradient(160deg, #7fa35a 0%, #c9b89c 45%, #e8d6c4 100%); }
  .photo--grandparents { left: 0; top: 320px; width: 236px; height: 235px; background: linear-gradient(160deg, #e9e6e2 0%, #d8b8a4 60%, #b89682 100%); }
  .photo--grandson { left: 0; top: 560px; width: 236px; height: 240px; background: linear-gradient(170deg, #c8b49e 0%, #eee9e4 55%, #2b4d9a 100%); }
  .photo--newborn { left: 300px; top: 790px; width: 445px; height: 410px; background: linear-gradient(150deg, #e9d8c8 0%, #caa08a 45%, #efe6df 100%); }
  .photo--grandpa-girl { left: 762px; top: 798px; width: 208px; height: 158px; background: linear-gradient(150deg, #9d7763 0%, #6b4a3a 60%, #d9d2cc 100%); }
  .photo--hug-bw { left: 978px; top: 790px; width: 222px; height: 200px; background: linear-gradient(150deg, #e8e8e8 0%, #8a8a8a 55%, #3d3d3d 100%); }
  .photo--trio-bw { left: 762px; top: 968px; width: 208px; height: 160px; background: linear-gradient(160deg, #d9d9d9 0%, #6e6e6e 60%, #2c2c2c 100%); }
  .photo--family-br { left: 978px; top: 1000px; width: 222px; height: 150px; background: linear-gradient(160deg, #efe4da 0%, #d7b29c 55%, #2c58b0 100%); }

  /* Central message */
  .message {
    position: absolute;
    left: 240px; top: 338px;
    width: 515px;
    font-family: "Roboto Condensed", "Arial Narrow", sans-serif;
    color: var(--ink);
    line-height: 1;
  }
  .message .row { display: block; font-size: 58px; padding-left: 26px; letter-spacing: -1px; }
  .message .row strong { font-weight: 700; }
  .message .band {
    display: block;
    margin-top: 8px;
    background: var(--ink);
    color: var(--white);
    font-size: 36px;
    padding: 2px 0 4px 26px;
  }
  .message .cancer {
    display: block;
    color: var(--green);
    font-size: 140px;
    padding-left: 22px;
    margin-top: 4px;
    letter-spacing: -3px;
  }
  .message .row--last { margin-top: 4px; font-size: 62px; }

  .rule { position: absolute; background: var(--ink); }
  .rule--horizontal { left: 240px; top: 722px; width: 515px; height: 16px; }
  .rule--vertical { left: 270px; top: 722px; width: 14px; height: 478px; }

  /* Right panel */
  .panel {
    position: absolute;
    left: 755px; top: 0;
    width: 445px; height: 785px;
    background: var(--panel);
  }
  .photo--bridge {
    left: 0; top: 0; width: 445px; height: 380px;
    background: linear-gradient(180deg, #7c7fd0 0%, #5d61b8 55%, var(--panel) 100%);
  }
  .panel-copy {
    position: absolute;
    right: 45px; top: 410px;
    text-align: right;
    color: var(--white);
  }
  .panel-copy .give { font-family: "Montserrat", sans-serif; font-weight: 700; font-size: 44px; line-height: 1; }
  .panel-copy .give span { font-family: "Roboto Condensed", sans-serif; font-weight: 400; }
  .panel-copy .gift { font-family: "Roboto Condensed", sans-serif; font-size: 32px; line-height: 1; }
  .panel-copy .knowledge { font-family: "Montserrat", sans-serif; font-weight: 700; font-size: 40px; line-height: 1; }
  .panel-copy .knowing {
    margin-top: 18px;
    font-family: "Comic Neue", "Comic Sans MS", cursive;
    font-weight: 700;
    font-size: 27px;
    line-height: 1.3;
  }
  .bulb { position: absolute; right: 52px; top: 645px; }
  .power {
    position: absolute;
    right: 45px; top: 728px;
    color: var(--green);
    font-family: "Montserrat", sans-serif;
    font-weight: 700;
    font-size: 20px;
  }
  .power::before {
    content: "";
    display: inline-block;
    width: 14px; height: 14px;
    background: var(--green);
    margin-right: 3px;
  }

  /* Brand */
  .brand {
    position: absolute;
    left: 38px; top: 910px;
    display: flex;
    align-items: center;
    gap: 12px;
  }
  .brand .dot { width: 62px; height: 62px; border-radius: 50%; background: var(--navy); }
  .brand .name {
    font-family: "Roboto", sans-serif;
    font-weight: 700;
    font-size: 24px;
    line-height: 1.05;
    color: var(--navy);
  }

  .site {
    position: absolute;
    right: 40px; top: 1160px;
    font-family: "Roboto", sans-serif;
    font-weight: 700;
    font-size: 23px;
    color: var(--ink);
  }
</style>
</head>
<body>
<main class="backdrop">

  <header class="title-block">
    <span class="line line--bold">Hereditary</span>
    <span class="line">Cancer</span>
    <span class="line">Screening</span>
    <span class="tagline">"The Test You Take For Them"</span>
  </header>

  <div class="photo photo--family-top" role="img" aria-label="Multi-generation family smiling together outdoors"></div>
  <div class="photo photo--grandparents" role="img" aria-label="Laughing grandparents close together"></div>
  <div class="photo photo--grandson" role="img" aria-label="Smiling young grandson with grandparents"></div>

  <section class="message">
    <span class="row">WILL YOU <strong>GIVE</strong></span>
    <span class="row">YOUR LOVED ONES</span>
    <span class="band">THE INFORMATION TO BEAT</span>
    <span class="cancer">CANCER</span>
    <span class="row row--last">IN THEIR LIVES ?</span>
  </section>

  <div class="rule rule--horizontal"></div>
  <div class="rule rule--vertical"></div>

  <div class="photo photo--newborn" role="img" aria-label="Grandparents and family gathered around a newborn baby"></div>

  <aside class="panel">
    <div class="photo photo--bridge" role="img" aria-label="Grandmother and grandchildren sitting on a wooden bridge in the woods, purple tint"></div>
    <div class="panel-copy">
      <div class="give">GIVE <span>THEM</span></div>
      <div class="gift">THE GIFT OF</div>
      <div class="knowledge">KNOWLEDGE</div>
      <div class="knowing">Knowing is better than<br>not knowing.</div>
    </div>
    <svg class="bulb" width="90" height="80" viewBox="0 0 90 80" aria-hidden="true">
      <g fill="none" stroke="#4cf01a" stroke-width="6" stroke-linecap="round">
        <circle cx="42" cy="42" r="17"/>
        <path d="M52 56 L62 70"/>
        <path d="M58 66 L68 60"/>
        <path d="M42 6 L42 16"/>
        <path d="M16 16 L23 23"/>
        <path d="M68 16 L61 23"/>
        <path d="M4 42 L14 42"/>
        <path d="M80 42 L70 42"/>
      </g>
    </svg>
    <div class="power">Knowledge is Power</div>
  </aside>

  <div class="photo photo--grandpa-girl" role="img" aria-label="Grandfather hugging his granddaughter"></div>
  <div class="photo photo--hug-bw" role="img" aria-label="Black and white photo of grandmother embracing granddaughter"></div>
  <div class="photo photo--trio-bw" role="img" aria-label="Black and white photo of grandparents with granddaughter"></div>
  <div class="photo photo--family-br" role="img" aria-label="Grandparents with grandchildren smiling"></div>

  <div class="brand">
    <span class="dot"></span>
    <span class="name">KINWARD<br>HEALTH<br>GROUP</span>
  </div>

  <div class="site">www.kinshipScreening.com</div>

</main>
</body>
</html>
```